Redesign of business card for Cedar Ridge Mechanical

We are looking for a new design for our business cards for Cedar Ridge Mechanical. We are a plumbing & HVAC construction company, operating on the West Coast of Canada and USA. Logo attached.
Industry/Entity Type
Construction - Plumbing & HVAC
Contact Information for Business Card
Name, address, phone numbers, email, website address
Look and feel
Each slider illustrates characteristics of the customer's brand and the style your logo design should communicate.

```html
<!DOCTYPE html>
<html lang="en">
<head>
<meta charset="utf-8">
<title>Cedar Ridge Mechanical – Business Card</title>
<link href="https://fonts.googleapis.com/css2?family=Poppins:wght@300;400;600;700&display=swap" rel="stylesheet">
<style>
  :root {
    --stage: #222222;
    --card-white: #ffffff;
    --card-dark: #1f1f21;
    --ink: #111111;
    --ink-soft: #333333;
    --light-text: #f2f2f2;
    --pattern-a: #2a2a2d;
    --pattern-b: #1a1a1c;
  }
  html, body {
    margin: 0;
    padding: 0;
    width: 1200px;
    height: 780px;
    overflow: hidden;
    background: var(--stage);
    font-family: "Poppins", sans-serif;
  }
  .stage {
    position: relative;
    width: 1200px;
    height: 780px;
  }
  .card {
    position: absolute;
    top: 230px;
    width: 560px;
    height: 320px;
    overflow: hidden;
    box-shadow: 0 18px 40px rgba(0,0,0,0.55);
  }
  .card--front { left: 30px; background: var(--card-white); }
  .card--back  { left: 610px; background: var(--card-dark); }

  .front-art { position: absolute; inset: 0; }

  .brand {
    position: absolute;
    top: 36px;
    right: 34px;
    display: flex;
    align-items: center;
    gap: 12px;
  }
  .brand__square {
    width: 34px;
    height: 34px;
    background: var(--ink);
  }
  .brand__name {
    font-weight: 600;
    font-size: 19px;
    line-height: 1.15;
    color: var(--ink);
    letter-spacing: 0.5px;
    text-transform: uppercase;
  }

  .person {
    position: absolute;
    left: 32px;
    top: 160px;
  }
  .person__name {
    margin: 0;
    font-size: 30px;
    line-height: 1;
    color: var(--ink);
    white-space: nowrap;
  }
  .person__first { font-weight: 700; }
  .person__last { font-weight: 300; }
  .person__title {
    margin: 6px 0 0;
    text-align: right;
    font-size: 14px;
    font-weight: 400;
    color: var(--ink-soft);
  }

  .divider {
    position: absolute;
    left: 300px;
    top: 102px;
    width: 1px;
    height: 76px;
    background: var(--ink);
  }

  .contact {
    position: absolute;
    left: 316px;
    top: 100px;
    margin: 0;
    padding: 0;
    list-style: none;
  }
  .contact__item {
    display: flex;
    align-items: center;
    gap: 8px;
    height: 26px;
    font-size: 13px;
    color: var(--ink);
    white-space: nowrap;
  }
  .contact__icon { width: 13px; height: 13px; flex: none; }

  .address {
    position: absolute;
    right: 28px;
    bottom: 10px;
    margin: 0;
    font-size: 13px;
    font-weight: 400;
    color: var(--light-text);
    letter-spacing: 0.3px;
    white-space: nowrap;
  }

  .back-pattern {
    position: absolute;
    inset: 0;
    background: linear-gradient(135deg, var(--pattern-a) 0%, var(--pattern-b) 100%);
  }
  .back-brand {
    position: absolute;
    left: 390px;
    top: 132px;
    display: flex;
    align-items: center;
    gap: 6px;
  }
  .back-brand__square {
    width: 12px;
    height: 12px;
    background: var(--light-text);
  }
  .back-brand__name {
    font-weight: 600;
    font-size: 9px;
    line-height: 1.2;
    color: var(--light-text);
    text-transform: uppercase;
    letter-spacing: 0.3px;
  }
</style>
</head>
<body>
<main class="stage">

  <section class="card card--front" aria-label="Business card front">
    <svg class="front-art" width="560" height="320" viewBox="0 0 560 320" aria-hidden="true">
      <path d="M0,320 L0,300 C220,300 430,260 560,200 L560,320 Z" fill="var(--card-dark)"/>
      <path d="M140,282 C320,270 465,232 552,182 C470,240 320,276 140,284 Z" fill="var(--card-dark)"/>
    </svg>

    <div class="brand">
      <span class="brand__square"></span>
      <span class="brand__name">Cedar Ridge<br>Mechanical</span>
    </div>

    <div class="person">
      <h1 class="person__name"><span class="person__first">Marta</span> <span class="person__last">Kovalenko</span></h1>
      <p class="person__title">Founder &amp; CEO</p>
    </div>

    <span class="divider"></span>

    <ul class="contact">
      <li class="contact__item">
        <svg class="contact__icon" viewBox="0 0 24 24" aria-hidden="true"><path fill="var(--ink)" d="M6.6 10.8a15.1 15.1 0 0 0 6.6 6.6l2.2-2.2a1 1 0 0 1 1-.25 11.4 11.4 0 0 0 3.6.57 1 1 0 0 1 1 1V20a1 1 0 0 1-1 1A17 17 0 0 1 3 4a1 1 0 0 1 1-1h3.5a1 1 0 0 1 1 1c0 1.250.2 2.450.57 3.57a1 1 0 0 1-.25 1z"/></svg>
        (604) 555-0142
      </li>
      <li class="contact__item">
        <svg class="contact__icon" viewBox="0 0 24 24" aria-hidden="true"><rect x="2" y="5" width="20" height="14" rx="1.5" fill="var(--ink)"/><path d="M3 6l9 7 9-7" stroke="#fff" stroke-width="1.6" fill="none"/></svg>
        info@cedarridgemech.com
      </li>
      <li class="contact__item">
        <svg class="contact__icon" viewBox="0 0 24 24" aria-hidden="true"><circle cx="12" cy="12" r="9.5" fill="none" stroke="var(--ink)" stroke-width="2"/><ellipse cx="12" cy="12" rx="4" ry="9.5" fill="none" stroke="var(--ink)" stroke-width="1.6"/><path d="M2.5 12h19" stroke="var(--ink)" stroke-width="1.6"/></svg>
        www.cedarridgemech.com
      </li>
    </ul>

    <p class="address">1480 Harbor Way Suite 300 Vancouver, BC V6B 2K4</p>
  </section>

  <section class="card card--back" aria-label="Business card back">
    <div class="back-pattern" role="img" aria-label="Faint repeating brand mark pattern across the dark card back"></div>
    <div class="back-brand">
      <span class="back-brand__square"></span>
      <span class="back-brand__name">Cedar Ridge<br>Mechanical</span>
    </div>
  </section>

</main>
</body>
</html>
```